creation of a business card design for a company specializing in the creation...

I would like to create a design for a professional business card on a black background and with the company's colors (I am attaching some files: including the logo in horizontal and centered format, I am also attaching a recent project design a T-shirt, this is the one I chose to give you an idea of my preferences.

we are in the process of developing a new website design, it is still in the development phase but it can be viewed at the following address: www.vantrelmo.be to give you other ideas about the company
you will see for yourself the subject of my main activity: company specializing in the construction of stairs

I would like a business card that stands out from the rest with a unique design

here is the informations
Name: Lucien Barthel
Function: Manager
Address: Rue Moulinet du Parc 42
7180 La Louvière
telephone: +32 468 219 804
email: info@rx7p.be
website: rx7p. be
social networks: Facebook, YouTube, TikTok, Instagram

Target Market(s)

customer who wants to have a beautiful staircase built

Industry/Entity Type

contruction d'escalier

Contact Information for Business Card

Adresse. Numero de telephone, site web, le texte : "Createur d'escalier", logo recto-verso, icone des reseaux sociaux

Requirements
Must have
• the mention: Stair creator
Nice to have
• an illustration of a designer staircase
Should not have
• do not distort the logo

```html
<!DOCTYPE html>
<html lang="en">
<head>
<meta charset="utf-8">
<title>RX7P business card</title>
<link rel="stylesheet" href="https://fonts.googleapis.com/css2?family=Montserrat:wght@400;500;700&display=swap">
<style>
  :root {
    --stage: #2a2b2f;
    --card: #151517;
    --card-edge: #6d98bd;
    --accent: #6f9cc4;
    --ink: #f2f2f2;
    --ink-soft: #c9c9cc;
  }
  * { margin: 0; padding: 0; box-sizing: border-box; }
  html, body { width: 1200px; height: 900px; overflow: hidden; }
  body {
    background: var(--stage);
    font-family: "Montserrat", sans-serif;
    color: var(--ink);
    display: flex;
    flex-direction: column;
    align-items: center;
    justify-content: center;
    gap: 44px;
  }
  .card {
    position: relative;
    width: 580px;
    height: 352px;
    background: var(--card);
    border-radius: 18px;
    border-bottom: 4px solid var(--card-edge);
    overflow: hidden;
  }

  /* brand lockup */
  .brand { display: flex; align-items: center; gap: 18px; }
  .brand-square { width: 58px; height: 58px; background: var(--accent); flex: none; }
  .brand-text { display: flex; flex-direction: column; }
  .brand-name {
    font-weight: 500;
    font-size: 58px;
    letter-spacing: 6px;
    line-height: 1;
    color: var(--ink);
  }
  .brand-tagline {
    margin-top: 8px;
    font-size: 11px;
    letter-spacing: 5.5px;
    color: var(--accent);
    text-transform: uppercase;
    white-space: nowrap;
  }

  .card-front .brand {
    position: absolute;
    left: 50%;
    top: 50%;
    transform: translate(-50%, -50%);
  }

  /* back side */
  .card-back .brand { position: absolute; left: 44px; top: 40px; }
  .card-back .brand-name { font-size: 44px; letter-spacing: 5px; }
  .card-back .brand-tagline { font-size: 9px; letter-spacing: 4.5px; margin-top: 6px; }

  .person {
    position: absolute;
    right: 44px;
    top: 40px;
    text-align: right;
  }
  .person-name { font-weight: 700; font-size: 24px; color: var(--accent); }
  .person-role { font-size: 13px; color: var(--ink); margin-top: 2px; }
  .accent-bar {
    position: absolute;
    right: 0;
    top: 36px;
    width: 12px;
    height: 40px;
    background: var(--accent);
  }

  .address {
    position: absolute;
    left: 44px;
    top: 160px;
    font-size: 14px;
    line-height: 1.35;
    color: var(--ink);
  }
  .contacts {
    position: absolute;
    left: 44px;
    top: 222px;
    list-style: none;
    font-size: 13.5px;
    line-height: 1;
  }
  .contacts li { display: flex; align-items: center; gap: 12px; margin-bottom: 9px; }
  .contacts svg { width: 14px; height: 14px; fill: var(--accent); flex: none; }
  .socials { position: absolute; left: 44px; bottom: 22px; display: flex; gap: 10px; }
  .social-tile { width: 16px; height: 16px; border-radius: 3px; background: var(--accent); }
</style>
</head>
<body>

  <section class="card card-front" aria-label="Card front">
    <div class="brand">
      <span class="brand-square"></span>
      <div class="brand-text">
        <span class="brand-name">RX7P</span>
        <span class="brand-tagline">Stair Creator</span>
      </div>
    </div>
  </section>

  <section class="card card-back" aria-label="Card back">
    <div class="brand">
      <div class="brand-text">
        <span class="brand-name">RX7P</span>
        <span class="brand-tagline">Stair Creator</span>
      </div>
    </div>

    <div class="person">
      <p class="person-name">Lucien Barthel</p>
      <p class="person-role">Manager</p>
    </div>
    <span class="accent-bar"></span>

    <p class="address">Rue Moulinet du Parc 42<br>7180 La Louvière</p>

    <ul class="contacts">
      <li>
        <svg viewBox="0 0 24 24" aria-hidden="true"><path d="M6.6 10.8a15.1 15.1 0 0 0 6.6 6.6l2.2-2.2a1 1 0 0 1 1-.25 11.4 11.4 0 0 0 3.6.57 1 1 0 0 1 1 1V20a1 1 0 0 1-1 1A17 17 0 0 1 3 4a1 1 0 0 1 1-1h3.5a1 1 0 0 1 1 1c0 1.25.2 2.45.57 3.6a1 1 0 0 1-.25 1z"/></svg>
        <span>+32 468 219 804</span>
      </li>
      <li>
        <svg viewBox="0 0 24 24" aria-hidden="true"><path d="M2 5h20v14H2zm2 2v.4l8 5 8-5V7zm0 2.8V17h16V9.8l-8 5z"/></svg>
        <span>info@rx7p.be</span>
      </li>
      <li>
        <svg viewBox="0 0 24 24" aria-hidden="true"><path d="M12 2a10 10 0 1 0 0 20 10 10 0 0 0 0-20zm6.9 6h-3a15.6 15.6 0 0 0-1.3-3.6A8 8 0 0 1 18.9 8zM12 4a14 14 0 0 1 1.9 4h-3.8A14 14 0 0 1 12 4zM4.3 14a8 8 0 0 1 0-4h3.4a16.5 16.5 0 0 0 0 4zm.8 2h3a15.6 15.6 0 0 0 1.3 3.6A8 8 0 0 1 5.1 16zm3-8h-3a8 8 0 0 1 4.3-3.6A15.6 15.6 0 0 0 8.1 8zM12 20a14 14 0 0 1-1.9-4h3.8A14 14 0 0 1 12 20zm2.3-6H9.7a14.7 14.7 0 0 1 0-4h4.6a14.7 14.7 0 0 1 0 4zm.3 5.6a15.6 15.6 0 0 0 1.3-3.6h3a8 8 0 0 1-4.3 3.6zM16.3 14a16.5 16.5 0 0 0 0-4h3.4a8 8 0 0 1 0 4z"/></svg>
        <span>www.rx7p. be</span>
      </li>
    </ul>

    <div class="socials" aria-label="Social networks">
      <span class="social-tile"></span>
      <span class="social-tile"></span>
      <span class="social-tile"></span>
      <span class="social-tile"></span>
    </div>
  </section>

</body>
</html>
```